New Business Card Design for Manufacturing

We are an engineering/manufacturing company that offers Advanced machining/assembly/engineering services, as well as innovative products for the heavy duty engine cooling markets.

We are looking to get a new business card designed that is clean and modern looking, but still fits the wide range of technical/skilled work we do.

- We hope to use this design as the base for other design work in new Presentations, web, and print work.

Industry/Entity Type

Engineering

Contact Information for Business Card

Our preferred color of blue is (RGB) 22/71/159 but can vary slightly from that color. Our content will be our Logo and full company name (Vantrell Forge Works, Inc.), company address, name, job title, phone number with extension, cell number, fax number, website, and email address on the cards.
We'd like the full company name next to the logo, but we are open to other interpretations of that layout.
Preferably, we would like the back side to be clean with just our logo, and the front to contain all of the contact information.

Colors
2f74b4
0355a3
85abd2

Requirements
Must have
• - Logo, company name, needed content - We are open to interpretation beyond that.
• - Standard size business card.
• - Horizontal orientation.
• - Enough space for lengthy names / job titles (for example, a job title could read "Directory of Human Resources" or "V.P. of Governmental Affairs"). We need this to look clean, whether the title be short (CEO) or long (as described above).

```html
<!DOCTYPE html>
<html lang="en">
<head>
<meta charset="utf-8">
<title>Vantrell Forge Works – Business Card</title>
<link rel="stylesheet" href="https://fonts.googleapis.com/css2?family=Lato:wght@400;700;900&family=Archivo+Black&display=swap">
<style>
  :root {
    --brand-blue: #0355a3;
    --mid-blue: #2f74b4;
    --soft-blue: #85abd2;
    --ink: #1c1c1c;
    --paper: #ffffff;
    --backdrop: #e9ebee;
  }
  * { margin: 0; padding: 0; box-sizing: border-box; }
  html, body {
    width: 1200px; height: 901px; overflow: hidden;
    background: var(--backdrop);
    font-family: "Lato", sans-serif;
  }
  .sheet {
    position: relative; width: 1200px; height: 901px;
    display: flex; align-items: center; justify-content: center; gap: 40px;
  }
  .card {
    position: relative; width: 540px; height: 309px; overflow: hidden;
    box-shadow: 0 10px 28px rgba(0,0,0,.18);
  }

  /* Back side */
  .card-back { background: var(--brand-blue); color: var(--paper); }
  .card-back .brand-name {
    position: absolute; left: 0; right: 0; top: 96px; text-align: center;
    font-weight: 900; font-size: 78px; letter-spacing: 1px; line-height: 1;
  }
  .card-back .web {
    position: absolute; left: 0; right: 0; bottom: 40px; text-align: center;
    font-size: 15px; letter-spacing: .5px;
  }

  /* Front side */
  .card-front { background: var(--paper); color: var(--ink); }
  .card-front .brand-name {
    position: absolute; left: 28px; top: 28px;
    font-weight: 900; font-size: 46px; line-height: 1; color: var(--brand-blue);
  }
  .company-name {
    position: absolute; left: 262px; top: 34px;
    font-family: "Archivo Black", sans-serif; font-size: 15px; line-height: 15px;
    text-transform: uppercase; color: var(--ink);
  }
  .company-name small { font-size: 7px; margin-left: 2px; }
  .person {
    position: absolute; right: 28px; top: 96px; text-align: right;
  }
  .person .name { font-weight: 700; font-size: 22px; color: var(--brand-blue); line-height: 1.1; }
  .person .title { font-size: 14px; margin-top: 3px; }
  .divider {
    position: absolute; left: 28px; right: 28px; top: 148px;
    height: 1px; background: var(--brand-blue);
  }
  .contacts {
    position: absolute; left: 28px; top: 160px; list-style: none;
    font-size: 13px; line-height: 19px;
  }
  .contacts li { display: flex; align-items: center; gap: 8px; }
  .contacts svg { width: 11px; height: 11px; fill: var(--brand-blue); }
  .address {
    position: absolute; right: 28px; top: 200px; text-align: right;
    font-size: 14px; line-height: 18px;
  }
  .footer-bands { position: absolute; left: 0; bottom: 0; width: 540px; height: 46px; }
  .card-front .web {
    position: absolute; right: 28px; bottom: 9px;
    font-size: 14px; color: var(--paper); letter-spacing: .3px;
  }
</style>
</head>
<body>
<main class="sheet">
  <section class="card card-back" aria-label="Card back">
    <div class="brand-name">Vantrell</div>
    <div class="web">www.vantrellforge.com</div>
  </section>

  <section class="card card-front" aria-label="Card front">
    <div class="brand-name">Vantrell</div>
    <div class="company-name">Vantrell<br>Forge<br>Works<small>Inc</small></div>

    <div class="person">
      <div class="name">Dana Kessler</div>
      <div class="title">Directory of Human Resources</div>
    </div>
    <div class="divider"></div>

    <ul class="contacts">
      <li><svg viewBox="0 0 12 12"><path d="M2.5 0.5l2 2.5-1.2 1.3c.8 1.7 2 2.9 3.7 3.7l1.3-1.2 2.5 2-1.2 1.8C5 10.6 1.4 7 .7 1.7z"/></svg>555 014 2200</li>
      <li><svg viewBox="0 0 12 12"><path d="M3 0h6a1 1 0 0 1 1 1v10a1 1 0 0 1-1 1H3a1 1 0 0 1-1-1V1a1 1 0 0 1 1-1zm.8 1.5v7.5h4.4V1.5z"/></svg>555 014 2201</li>
      <li><svg viewBox="0 0 12 12"><path d="M3 0h6v3H3zM1 4h10a1 1 0 0 1 1 1v4H10v3H2V9H0V5a1 1 0 0 1 1-1zm2.5 5v1.5h5V9z"/></svg>555 014 2203</li>
      <li><svg viewBox="0 0 12 12"><path d="M0 2h12v8H0zM1 3l5 3.5L11 3z" fill-rule="evenodd"/></svg>info@vantrellforge.com</li>
    </ul>

    <div class="address">418 Larkspur Road<br>Alden, TX 77590</div>

    <svg class="footer-bands" viewBox="0 0 540 46" aria-hidden="true">
      <path d="M0 8h230v38H0z" fill="var(--soft-blue)"/>
      <path d="M200 46C212 14 228 6 262 6H540v40z" fill="var(--brand-blue)"/>
    </svg>
    <div class="web">www.vantrellforge.com</div>
  </section>
</main>
</body>
</html>
```